Black Matte card with samurai logo which I would like it to be textured and company name on one side and on the other side I would like the company information with the reno (Face logo) Sushi logo. Double Sided card.

majority customers are University students, University sororities and fraternities.

It Company

Reno Sushi
317 W. Harlow Ave
Tucson, AZ 85042
Phone (520)413-6271
Fax (520)357-1846
E-mail: Renosushidesert@mailbox-example.com
FB: Renosushidesert
Twitter: Renosushidesert

• Present Normal

```html
<!DOCTYPE html>
<html lang="en">
<head>
<meta charset="utf-8">
<title>Reno Sushi — Business Card</title>
<link rel="stylesheet" href="https://fonts.googleapis.com/css2?family=PT+Sans:wght@400&display=swap">
<style>
  :root {
    --backdrop: #e9e6e1;
    --card-black: #1b1b1b;
    --card-black-light: #3a3a3a;
    --card-white: #ffffff;
    --brand-red: #b3261e;
    --brand-dark: #2b2b2b;
    --ink: #444444;
    --divider: #d6d6d6;
    --band-black: #1e1e1e;
  }
  * { box-sizing: border-box; margin: 0; padding: 0; }
  html, body {
    width: 1200px; height: 1124px; overflow: hidden;
    background: var(--backdrop);
    font-family: "PT Sans", Arial, sans-serif;
  }
  .card {
    position: absolute;
    width: 873px; height: 497px;
    border-radius: 34px;
    overflow: hidden;
    box-shadow: 0 4px 14px rgba(0,0,0,.25);
  }
  /* Front */
  .card--front {
    left: 51px; top: 43px;
    background: linear-gradient(180deg, var(--card-black-light) 0%, var(--card-black) 45%, #262626 70%, var(--card-black) 100%);
  }
  .card--front .mascot {
    position: absolute; left: 278px; top: 41px;
    width: 307px; height: 277px;
    background: radial-gradient(ellipse at center, #5a5a5a 0%, #3b3b3b 55%, rgba(40,40,40,0) 80%);
    border-radius: 12px;
  }
  .card--front .brand-name {
    position: absolute; left: 0; right: 0; top: 340px;
    text-align: center;
    font-size: 80px; font-weight: 400;
    color: var(--brand-red);
    letter-spacing: 1px;
  }
  /* Back */
  .card--back {
    left: 253px; top: 565px;
    background: var(--card-white);
  }
  .card--back .mascot {
    position: absolute; left: 135px; top: 43px;
    width: 212px; height: 190px;
    background: radial-gradient(ellipse at center, #6b6b6b 0%, #d9d9d9 60%, rgba(255,255,255,0) 80%);
    border-radius: 10px;
  }
  .card--back .brand-name {
    position: absolute; left: 120px; width: 245px; top: 236px;
    text-align: center;
    font-weight: 400;
    line-height: 1;
  }
  .brand-name__main { display: block; font-size: 70px; color: var(--brand-red); }
  .brand-name__sub { display: block; font-size: 40px; margin-top: -4px; color: var(--brand-dark); }
  .divider {
    position: absolute; left: 390px; top: 70px;
    width: 1px; height: 278px;
    background: var(--divider);
  }
  .contact-list {
    position: absolute; left: 410px; top: 84px;
    list-style: none;
  }
  .contact-list li {
    display: flex; align-items: center;
    height: 33px;
    font-size: 22px; color: var(--ink);
  }
  .contact-list .icon {
    width: 20px; height: 20px; margin-right: 12px; flex: none;
  }
  .contact-list .icon--square {
    width: 18px; height: 18px; margin: 0 13px 0 1px;
    background: #4a6aa5; border-radius: 3px;
  }
  .contact-list .icon--square-light { background: #5aa9d6; }
  .address {
    position: absolute; left: 410px; top: 276px;
    font-size: 22px; line-height: 32px; color: var(--ink);
  }
  .footer-band {
    position: absolute; left: 0; bottom: 0;
    width: 873px; height: 130px;
    background: linear-gradient(180deg, var(--brand-red) 0%, #6a1a16 45%, var(--band-black) 100%);
  }
</style>
</head>
<body>

<section class="card card--front">
  <div class="mascot" role="img" aria-label="Samurai mascot illustration holding a sword and a fish, in black, white and red"></div>
  <p class="brand-name">reno sushi</p>
</section>

<section class="card card--back">
  <div class="mascot" role="img" aria-label="Samurai mascot illustration holding a sword and a fish"></div>
  <p class="brand-name">
    <span class="brand-name__main">reno</span>
    <span class="brand-name__sub">sushi</span>
  </p>

  <div class="divider"></div>

  <ul class="contact-list">
    <li>
      <svg class="icon" viewBox="0 0 20 20" aria-hidden="true"><circle cx="10" cy="10" r="9" fill="none" stroke="#b3261e" stroke-width="1.6"/><path d="M6.5 5.5l2 0 .8 2.4-1.3 1c.6 1.3 1.5 2.2 2.6 2.7l1-1.3 2.4.8v2c-4.5.3-7.8-3-7.5-7.6z" fill="#b3261e"/></svg>
      (520)413-6271
    </li>
    <li>
      <svg class="icon" viewBox="0 0 20 20" aria-hidden="true"><rect x="5.5" y="2" width="9" height="16" rx="1.5" fill="#b3261e"/><rect x="7" y="4" width="6" height="5" fill="#fff"/><g fill="#fff"><rect x="7" y="10.5" width="1.6" height="1.4"/><rect x="9.2" y="10.5" width="1.6" height="1.4"/><rect x="11.4" y="10.5" width="1.6" height="1.4"/><rect x="7" y="13" width="1.6" height="1.4"/><rect x="9.2" y="13" width="1.6" height="1.4"/><rect x="11.4" y="13" width="1.6" height="1.4"/></g></svg>
      (520)357-1846
    </li>
    <li>
      <svg class="icon" viewBox="0 0 20 20" aria-hidden="true"><rect x="1.5" y="5" width="17" height="11" rx="1" fill="#b3261e"/><path d="M2 5.5l8 6 8-6" fill="none" stroke="#fff" stroke-width="1.4"/></svg>
      Renosushidesert@mailbox-example.com
    </li>
    <li><span class="icon icon--square"></span>Renosushidesert</li>
    <li><span class="icon icon--square icon--square-light"></span>Renosushidesert</li>
  </ul>

  <p class="address">Reno Sushi 317 W. Harlow Ave Tucson<br>AZ 85042</p>

  <div class="footer-band" role="img" aria-label="Decorative red and black curved bands along the bottom edge"></div>
</section>

</body>
</html>
```